Stationery Design Project for Nimbora, Chicago

Nimbora, a street parking application which helps car drivers find a street parking spot by offering an ideal path along which to look for parking. This path is calculated by our algorithm based on data (e.g. historical data, baseball games schedule, etc.). Along this path the driver will find a spot and will also save 70% of the search time. Customer we target is reg. between 21 and 45 yo.

We envision something young, fresh, bright and original. Slightly abstract maybe. It should represent the idea and elements of finding street parking in the city, e.g. car(s), parking spot, people, city, etc. (just ideas!).

Logo is attached.

Requirement:
- Business Cards (2 Sided Full Color CMYK)
- Letterhead (1 Sided Full Color CMYK)
- Envelope (1 Sided Full Color CMYK)
- Sticker (1 Sided Full Color CMYK), round with a 2inch diameter.

Reason: We're starting to get more and more designs and need more time to look into all of them. Very exciting!! Thanks to everybody!

Hi all, we're in the process of selecting our favs. Though choices!!! Really good submissions. Will keep you posted and sorry for the delay.

Target Market(s)

Car drivers and owners between 21 and 45

Industry/Entity Type

Parking

Requirements
Must have
• Sticker should be round and include company URL nimbora.com and the new logo which we will attach soon.
Should not have
• Should not be too serious or boring.

```html
<!DOCTYPE html>
<html lang="en">
<head>
<meta charset="utf-8">
<title>Nimbora Business Card</title>
<link rel="stylesheet" href="https://fonts.googleapis.com/css2?family=Open+Sans:wght@400;600;700&display=swap">
<style>
  :root {
    --backdrop: #e9e9e9;
    --card: #ffffff;
    --brand-blue: #1f4fc4;
    --brand-blue-light: #3d7be6;
    --ink-dark: #1e1e1e;
    --ink-mid: #555555;
    --ink-soft: #666666;
    --shadow: rgba(0, 0, 0, 0.28);
  }
  * { margin: 0; padding: 0; box-sizing: border-box; }
  html, body { width: 954px; height: 1200px; overflow: hidden; }
  body {
    position: relative;
    background: var(--backdrop);
    font-family: "Open Sans", Arial, sans-serif;
    color: var(--ink-mid);
  }
  .card {
    position: absolute;
    left: 74px;
    width: 796px;
    height: 455px;
    background: var(--card);
    border-radius: 28px;
    box-shadow: 4px 6px 10px var(--shadow);
  }
  .card--front { top: 110px; }
  .card--back { top: 648px; }

  .brand-dot {
    position: absolute;
    border-radius: 50%;
    background: radial-gradient(circle at 40% 35%, var(--brand-blue-light), var(--brand-blue) 70%);
  }
  .card--front .brand-dot { left: 92px; top: 50px; width: 250px; height: 250px; }
  .card--back .brand-dot { left: 133px; top: 139px; width: 150px; height: 150px; }

  .brand-name {
    position: absolute;
    font-weight: 600;
    color: var(--ink-dark);
    letter-spacing: 1px;
    line-height: 1;
  }
  .card--front .brand-name { left: 470px; top: 36px; font-size: 62px; }
  .card--back .brand-name { left: 310px; top: 164px; font-size: 92px; }

  .holder { position: absolute; left: 471px; top: 208px; }
  .holder__name { font-size: 24px; font-weight: 700; color: var(--ink-mid); line-height: 30px; }
  .holder__role { font-size: 19px; font-weight: 700; color: var(--ink-mid); line-height: 28px; }

  .contact-list { position: absolute; left: 470px; top: 297px; list-style: none; }
  .contact-list li {
    display: flex; align-items: center;
    height: 31.5px; font-size: 19px; color: var(--ink-mid);
  }
  .contact-list svg { width: 20px; height: 18px; margin-right: 12px; fill: var(--ink-mid); }

  .address {
    position: absolute; left: 92px; width: 250px; top: 371px;
    text-align: center; font-size: 19px; line-height: 27px; color: var(--ink-mid);
    white-space: nowrap;
  }

  .web-line {
    position: absolute; left: 0; right: 0; top: 381px;
    text-align: center; font-size: 19px; color: var(--ink-mid);
    padding-right: 6px;
  }
  .web-line b { font-weight: 700; }
  .web-line .sep { margin: 0 10px; }
</style>
</head>
<body>

<section class="card card--front">
  <div class="brand-dot"></div>
  <div class="brand-name">Nimbora</div>

  <div class="holder">
    <p class="holder__name">Your Name</p>
    <p class="holder__role">Designation</p>
  </div>

  <ul class="contact-list">
    <li>
      <svg viewBox="0 0 20 18" aria-hidden="true"><path d="M2 6c0-3 4-4 8-4s8 1 8 4v1h-4V5H6v2H2z"/><rect x="4" y="8" width="12" height="8" rx="1"/></svg>
      123-456-7890
    </li>
    <li>
      <svg viewBox="0 0 20 18" aria-hidden="true"><rect x="5" y="1" width="10" height="5"/><rect x="1" y="6" width="18" height="8" rx="1"/><rect x="5" y="11" width="10" height="6" fill="#fff" stroke="#555" stroke-width="1.5"/></svg>
      123-456-7890
    </li>
    <li>
      <svg viewBox="0 0 20 18" aria-hidden="true"><path d="M2 4h16v12H2z" fill="none" stroke="#555" stroke-width="1.6"/><path d="M2 4l8 7 8-7" fill="none" stroke="#555" stroke-width="1.6"/></svg>
      name@website.com
    </li>
    <li>
      <svg viewBox="0 0 20 18" aria-hidden="true"><circle cx="10" cy="9" r="7"/><path d="M3 9h14M10 2c-3 3-3 11 0 14M10 2c3 3 3 11 0 14" fill="none" stroke="#fff" stroke-width="1"/></svg>
      www.website.com
    </li>
  </ul>

  <p class="address">City Name, Street Name<br>State Name, Country Code</p>
</section>

<section class="card card--back">
  <div class="brand-dot"></div>
  <div class="brand-name">Nimbora</div>
  <p class="web-line"><b>e</b> : name@website.com<span class="sep">|</span><b>w</b> : www.website.com</p>
</section>

</body>
</html>
```